Change color scheme of existing flyers

Hello! We recently re-branded our company with an awesome logo from Draft Lantern.
We changed our color scheme from Orange/Black to Red/Blue/Gray as you will see in the attachments.
We have a 4 page flyer that we need to incorporate the new colors into and have them look nice.
The pages are bound so the colors must flow well from page to page.
Please don't just replace logo, change orange to red, and submit. I designed the current flyers and can do that in 10 minutes. I'm looking for some great ideas to implement and make the flyers look as good as the new logo.:-)
This is a fun project but I have no time at the moment so I need your help.
I am attaching the old pdf versions and the new logo options for consideration.
Look forward to some creative input. Thanks!

Target Market(s)

Manufacturers

Industry/Entity Type

It Company

Requirements
Must have
• Must have flow from page to page similar to old black/orange version
Nice to have
• We like the current configuration but are open to new designs also

```html
<!DOCTYPE html>
<html lang="en">
<head>
<meta charset="utf-8">
<title>Norvex Air Supply Company – Ductboard &amp; Register Boxes</title>
<link href="https://fonts.googleapis.com/css2?family=Arimo:wght@400;700&display=swap" rel="stylesheet">
<style>
  :root{
    --red:#e0202b;
    --blue:#1f5aa6;
    --ink:#333333;
    --muted:#666666;
    --rule:#b5b5b5;
    --paper:#ffffff;
    --photo-light:#e4e6ea;
    --photo-dark:#9aa0a8;
  }
  *{box-sizing:border-box;margin:0;padding:0}
  html,body{width:929px;height:1200px;overflow:hidden;background:var(--paper)}
  body{font-family:"Arimo",Arial,sans-serif;color:var(--ink);position:relative}

  .site-header{position:absolute;left:0;top:0;width:929px;height:130px}
  .site-url{position:absolute;left:54px;top:33px;font-size:15px;font-weight:700;color:var(--muted)}
  .services{position:absolute;left:54px;top:65px;font-size:13px;line-height:21px;color:var(--muted);list-style:none}
  .brand{position:absolute;right:24px;top:22px;text-align:right}
  .brand-name{display:flex;align-items:center;justify-content:flex-end;gap:12px;font-size:58px;font-weight:700;color:var(--red);letter-spacing:2px;line-height:1}
  .brand-dot{width:26px;height:26px;border-radius:50%;background:var(--blue)}
  .brand-tagline{margin-top:8px;font-size:15px;font-weight:700;color:var(--blue);letter-spacing:.5px}

  .catalog{position:absolute;left:41px;top:134px;width:877px;display:grid;grid-template-columns:285px 285px 287px;grid-template-rows:505px 525px;gap:10px}
  .product{border:2px solid var(--rule);padding:14px 12px 10px 14px;font-size:10.5px;line-height:13px}
  .product-title{font-size:20px;line-height:21px;font-weight:400;color:var(--red);text-transform:uppercase;letter-spacing:-.3px}
  .product-photo{display:block;margin:14px 0 0 22px;width:200px;height:130px;border-radius:6px;background:linear-gradient(150deg,var(--photo-light),var(--photo-dark))}
  .features{list-style:none;margin-top:12px;color:var(--ink)}
  .features li::before{content:"• "}
  .grade{margin-top:14px;font-weight:700;color:var(--red);font-size:11px}
  table{border-collapse:collapse;width:100%}
  th{font-weight:700;text-align:left;color:var(--ink);padding:0}
  td{padding:0;white-space:nowrap}
  .num{text-align:center;width:17px}
  .part{width:30%}
  .wide .part{width:33%}
</style>
</head>
<body>
<header class="site-header">
  <div class="site-url">www.norvexair.com</div>
  <ul class="services">
    <li>• Security cages • Ductboard projects • Tank stands</li>
    <li>• Condenser wall brackets</li>
  </ul>
  <div class="brand">
    <div class="brand-name"><span class="brand-dot"></span>NORVEX</div>
    <div class="brand-tagline">AIR SUPPLY COMPANY</div>
  </div>
</header>

<main class="catalog">
  <section class="product">
    <h2 class="product-title">Ductboard<br>Triangle Boxes</h2>
    <div class="product-photo" role="img" aria-label="Photo of a foil-faced ductboard triangle box with labelled sides A to D"></div>
    <ul class="features"><li>R6 or R8 ductboard.</li><li>Assembled (unassembled available).</li><li>Seams taped with Corvane 181.</li><li>Staples used on all staple flaps.</li><li>Typical bundles of 6.</li></ul>
    <p class="grade">R6</p>
    <table><tr><th class="part">Part #</th><th>Description</th><th class="num">A</th><th class="num">B</th><th class="num">C</th><th class="num">D</th></tr>
      <tr><td>30-T10A</td><td>Triangle box-1</td><td class="num">15</td><td class="num">15</td><td class="num">15</td><td class="num">12</td></tr>
      <tr><td>30-T20A</td><td>Triangle box-2</td><td class="num">15</td><td class="num">15</td><td class="num">15</td><td class="num">15</td></tr>
      <tr><td>30-T30A</td><td>Triangle box-3</td><td class="num">19</td><td class="num">19</td><td class="num">19</td><td class="num">18</td></tr>
      <tr><td>30-T40A</td><td>Triangle box-4</td><td class="num">19</td><td class="num">19</td><td class="num">19</td><td class="num">23</td></tr></table>
    <p class="grade">R8</p>
    <table><tr><th class="part">Part #</th><th>Description</th><th class="num">A</th><th class="num">B</th><th class="num">C</th><th class="num">D</th></tr>
      <tr><td>30-T18</td><td>Triangle box-1 R8</td><td class="num">19</td><td class="num">19</td><td class="num">19</td><td class="num">15</td></tr>
      <tr><td>30-T28</td><td>Triangle box-2 R8</td><td class="num">19</td><td class="num">19</td><td class="num">19</td><td class="num">20</td></tr>
      <tr><td>30-T38</td><td>Triangle box-3 R8</td><td class="num">21</td><td class="num">21</td><td class="num">21</td><td class="num">23</td></tr></table>
  </section>

  <section class="product">
    <h2 class="product-title">Ductboard<br>Reducer Boxes</h2>
    <div class="product-photo" role="img" aria-label="Photo of a foil-faced ductboard reducer box with labelled sides A to D"></div>
    <ul class="features"><li>R6 or R8 ductboard.</li><li>Assembled (unassembled available).</li><li>Seams taped with Corvane 181.</li><li>Staples used on all staple flaps.</li><li>Typical bundles of 6.</li></ul>
    <p class="grade">R6</p>
    <table><tr><th class="part">Part #</th><th>Description</th><th class="num">A</th><th class="num">B</th><th class="num">C</th><th class="num">D</th></tr>
      <tr><td>30-R10A</td><td>Reducer box-1</td><td class="num">18</td><td class="num">10</td><td class="num">10</td><td class="num">12</td></tr>
      <tr><td>30-R20A</td><td>Reducer box-2</td><td class="num">18</td><td class="num">14</td><td class="num">14</td><td class="num">15</td></tr>
      <tr><td>30-R30A</td><td>Reducer box-3</td><td class="num">18</td><td class="num">14</td><td class="num">18</td><td class="num">23</td></tr>
      <tr><td>30-R40A</td><td>Reducer box-4</td><td class="num">20</td><td class="num">16</td><td class="num">16</td><td class="num">20</td></tr></table>
    <p class="grade">R8</p>
    <table><tr><th class="part">Part #</th><th>Description</th><th class="num">A</th><th class="num">B</th><th class="num">C</th><th class="num">D</th></tr>
      <tr><td>30-R18</td><td>Reducer box-1 R8</td><td class="num">16</td><td class="num">12</td><td class="num">12</td><td class="num">15</td></tr>
      <tr><td>30-R28</td><td>Reducer box-2 R8</td><td class="num">18</td><td class="num">14</td><td class="num">14</td><td class="num">15</td></tr>
      <tr><td>30-R38</td><td>Reducer box-3 R8</td><td class="num">20</td><td class="num">16</td><td class="num">16</td><td class="num">20</td></tr></table>
  </section>

  <section class="product wide">
    <h2 class="product-title">Ductboard<br>Cube Boxes</h2>
    <div class="product-photo" role="img" aria-label="Photo of a foil-faced ductboard cube box with labelled sides A to C"></div>
    <ul class="features"><li>R6 or R8 ductboard.</li><li>Assembled (unassembled available).</li><li>Seams taped with Corvane 181.</li><li>Staples used on all staple flaps.</li></ul>
    <p class="grade">R6</p>
    <table><tr><th class="part">Part #</th><th>Description</th><th class="num">A</th><th class="num">B</th><th class="num">C</th></tr>
      <tr><td>30-CU12</td><td>Cube 12x12 ID</td><td class="num">15</td><td class="num">15</td><td class="num">15</td></tr>
      <tr><td>30-CU14</td><td>Cube 14x14 ID</td><td class="num">15</td><td class="num">15</td><td class="num">15</td></tr>
      <tr><td>30-CU16</td><td>Cube 16x16 ID</td><td class="num">17</td><td class="num">17</td><td class="num">17</td></tr>
      <tr><td>30-CU18</td><td>Cube 18x18 ID</td><td class="num">19</td><td class="num">19</td><td class="num">19</td></tr>
      <tr><td>30-CU20</td><td>Cube 20x20 ID</td><td class="num">21</td><td class="num">21</td><td class="num">21</td></tr>
      <tr><td></td><td></td><td class="num">23</td><td class="num">23</td><td class="num">23</td></tr></table>
    <p class="grade">R8</p>
    <table><tr><th class="part">Part #</th><th>Description</th><th class="num">A</th><th class="num">B</th><th class="num">C</th></tr>
      <tr><td>30-CU12-R8</td><td>Cube 12x12 ID R8</td><td class="num">16</td><td class="num">16</td><td class="num">16</td></tr>
      <tr><td>30-CU14-R8</td><td>Cube 14x14 ID R8</td><td class="num">18</td><td class="num">18</td><td class="num">18</td></tr>
      <tr><td>30-CU16-R8</td><td>Cube 16x16 ID R8</td><td class="num">20</td><td class="num">20</td><td class="num">20</td></tr>
      <tr><td>30-CU18-R8</td><td>Cube 18x18 ID R8</td><td class="num">22</td><td class="num">22</td><td class="num">22</td></tr>
      <tr><td>30-CU20-R8</td><td>Cube 20x20 ID R8</td><td class="num">24</td><td class="num">24</td><td class="num">24</td></tr></table>
  </section>

  <section class="product wide">
    <h2 class="product-title">Ductboard<br>Mixing Boxes</h2>
    <div class="product-photo" role="img" aria-label="Photo of a foil-faced ductboard mixing box with labelled sides A to C"></div>
    <ul class="features"><li>R6 or R8 ductboard.</li><li>Assembled (unassembled available).</li><li>Seams taped with Corvane 181.</li><li>Staples used on all staple flaps.</li></ul>
    <p class="grade">R6</p>
    <table><tr><th class="part">Part #</th><th>Description</th><th class="num">A</th><th class="num">B</th><th class="num">C</th></tr>
      <tr><td>30-M12A</td><td>Mix Box 12x12 ID</td><td class="num">15</td><td class="num">15</td><td class="num">22</td></tr>
      <tr><td>30-M14A</td><td>Mix Box 14x14 ID</td><td class="num">17</td><td class="num">17</td><td class="num">22</td></tr>
      <tr><td>30-M16A</td><td>Mix Box 16x16 ID</td><td class="num">19</td><td class="num">19</td><td class="num">22</td></tr>
      <tr><td>30-M18A</td><td>Mix Box 18x18 ID</td><td class="num">21</td><td class="num">21</td><td class="num">22</td></tr>
      <tr><td>30-M20A</td><td>Mix Box 20x20 ID</td><td class="num">23</td><td class="num">23</td><td class="num">22</td></tr></table>
    <p class="grade">R8</p>
    <table><tr><th class="part">Part #</th><th>Description</th><th class="num">A</th><th class="num">B</th><th class="num">C</th></tr>
      <tr><td>30-M12A-R8</td><td>Mix Box 12x12 ID R8</td><td class="num">16</td><td class="num">16</td><td class="num">22</td></tr>
      <tr><td>30-M14A-R8</td><td>Mix Box 14x14 ID R8</td><td class="num">18</td><td class="num">18</td><td class="num">22</td></tr>
      <tr><td>30-M16A-R8</td><td>Mix Box 16x16 ID R8</td><td class="num">20</td><td class="num">20</td><td class="num">22</td></tr>
      <tr><td>30-M18A-R8</td><td>Mix Box 18x18 ID R8</td><td class="num">22</td><td class="num">22</td><td class="num">22</td></tr>
      <tr><td>30-M20A-R8</td><td>Mix Box 20x20 ID R8</td><td class="num">24</td><td class="num">24</td><td class="num">22</td></tr></table>
  </section>

  <section class="product wide">
    <h2 class="product-title">Register Boxes<br>Supply</h2>
    <div class="product-photo" role="img" aria-label="Photo of a supply register box with labelled sides A to C"></div>
    <ul class="features"><li>R6 or R8 ductboard.</li><li>Fully assembled.</li><li>Seams taped with Corvane 181.</li><li>Custom sizes available.</li></ul>
    <p class="grade">R6</p>
    <table><tr><th class="part">Part #</th><th>Description</th><th class="num">A</th><th class="num">B</th><th class="num">C</th></tr>
      <tr><td>30-0804-11</td><td>Supply Register Box</td><td class="num">08</td><td class="num">04</td><td class="num">11</td></tr>
      <tr><td>30-1006-11</td><td>Supply Register Box</td><td class="num">10</td><td class="num">06</td><td class="num">11</td></tr>
      <tr><td>30-1206-11</td><td>Supply Register Box</td><td class="num">12</td><td class="num">06</td><td class="num">11</td></tr>
      <tr><td>30-1406-11</td><td>Supply Register Box</td><td class="num">14</td><td class="num">06</td><td class="num">11</td></tr>
      <tr><td>30-1408-11</td><td>Supply Register Box</td><td class="num">14</td><td class="num">08</td><td class="num">11</td></tr></table>
    <p class="grade">R8</p>
    <table><tr><th class="part">Part #</th><th>Description</th><th class="num">A</th><th class="num">B</th><th class="num">C</th></tr>
      <tr><td>30-0804-11-R8</td><td>Supply Register Box</td><td class="num">08</td><td class="num">04</td><td class="num">11</td></tr>
      <tr><td>30-1006-11-R8</td><td>Supply Register Box</td><td class="num">10</td><td class="num">06</td><td class="num">11</td></tr>
      <tr><td>30-1206-11-R8</td><td>Supply Register Box</td><td class="num">12</td><td class="num">06</td><td class="num">11</td></tr>
      <tr><td>30-1406-11-R8</td><td>Supply Register Box</td><td class="num">14</td><td class="num">06</td><td class="num">11</td></tr>
      <tr><td>30-1408-11-R8</td><td>Supply Register Box</td><td class="num">14</td><td class="num">08</td><td class="num">11</td></tr></table>
  </section>

  <section class="product wide">
    <h2 class="product-title">Register Boxes<br>Return</h2>
    <div class="product-photo" role="img" aria-label="Photo of a return register box with labelled sides A to C"></div>
    <ul class="features"><li>R6 or R8 ductboard.</li><li>Fully assembled.</li><li>Seams taped with Corvane 181.</li><li>Custom sizes available.</li></ul>
    <p class="grade">R6</p>
    <table><tr><th class="part">Part #</th><th>Description</th><th class="num">A</th><th class="num">B</th><th class="num">C</th></tr>
      <tr><td>35-1414-35</td><td>Return Register Box</td><td class="num">14</td><td class="num">14</td><td class="num">4</td></tr>
      <tr><td>35-1616-35</td><td>Return Register Box</td><td class="num">16</td><td class="num">16</td><td class="num">4</td></tr>
      <tr><td>35-1818-35</td><td>Return Register Box</td><td class="num">18</td><td class="num">18</td><td class="num">4</td></tr>
      <tr><td>35-2020-35</td><td>Return Register Box</td><td class="num">20</td><td class="num">20</td><td class="num">4</td></tr>
      <tr><td>35-2424-35</td><td>Return Register Box</td><td class="num">24</td><td class="num">24</td><td class="num">4</td></tr></table>
    <p class="grade">R8</p>
    <table><tr><th class="part">Part #</th><th>Description</th><th class="num">A</th><th class="num">B</th><th class="num">C</th></tr>
      <tr><td>35-1414-35-R8</td><td>Return Register Box</td><td class="num">14</td><td class="num">14</td><td class="num">4</td></tr>
      <tr><td>35-1616-35-R8</td><td>Return Register Box</td><td class="num">16</td><td class="num">16</td><td class="num">4</td></tr>
      <tr><td>35-1818-35-R8</td><td>Return Register Box</td><td class="num">18</td><td class="num">18</td><td class="num">4</td></tr>
      <tr><td>35-2020-35-R8</td><td>Return Register Box</td><td class="num">20</td><td class="num">20</td><td class="num">4</td></tr>
      <tr><td>35-2424-35-R8</td><td>Return Register Box</td><td class="num">24</td><td class="num">24</td><td class="num">4</td></tr></table>
  </section>
</main>
</body>
</html>
```